Etiketten für Olivenöl-Intensivcreme
Zielgruppe
Wir produzieren Bio-Food, u.a. Wein und Olivenöl. Jetzt soll eine Olivenöl-Intensivcreme im Bereich Kosmetik auf dem Markt platziert werden. Unsere Zielgruppe hat ein sehr breites Altersspektrum (jung bis alt), ist naturverbunden, tierlieb, gebildet, kritisch-reflektierend, weiß gute Qualität zu schätzen, ist überwiegend weiblich. Die Olivenöl-Intensivcreme hat eine sehr breite Verwendung und soll sich als 'Allzweckwaffe' in jedem Haushalt etablieren (Babyhaut-Pflege, Lippenpflege, Ganzkörperpflege, Hand-Schutzcreme etc.).
Aufgabenstellung
Die Creme soll heißen: Velamira (es könnte z.B. der Buchstabe 'O' durch eine Olive ersetzt werden). Es gibt zwei Etikette (Deckeloberseite der Metalldose und auf dem Boden). Der Durchmesser der Etikette ist jeweils 5,5 cm. Die Deckelunterseite gilt reinen Pflichtangaben. Im Dateidownloadbereich sind die Textvorgaben für die Etikette. MUT zur Farbe! Wir sind NICHT brav und angepasst! Orange kann Akzente setzen bzw. für Aufmerksamkeit im Regal sorgen.

```html
<!DOCTYPE html>
<html lang="de">
<head>
<meta charset="utf-8">
<title>Velamira – Etiketten</title>
<link href="https://fonts.googleapis.com/css2?family=Amatic+SC:wght@700&family=Arvo&family=Raleway:wght@400&family=Rubik:wght@400;600&display=swap" rel="stylesheet">
<style>
  :root{
    --orange:#ee8252;
    --ink:#111111;
    --paper:#ffffff;
    --rim:#8a8a8a;
    --branch-area:#f3a680;
  }
  html,body{margin:0;padding:0;overflow:hidden;background:var(--paper);}
  .canvas{position:relative;width:1200px;height:727px;overflow:hidden;background:var(--paper);}
  .labels{position:absolute;inset:0;}
  .brand-top{font-family:"Raleway",sans-serif;font-size:24px;fill:var(--paper);letter-spacing:.5px;}
  .product-name{font-family:"Arvo",serif;font-size:74px;fill:var(--paper);}
  .hand{font-family:"Amatic SC",cursive;font-weight:700;}
  .badge-text{font-size:31px;fill:var(--paper);}
  .subtitle{font-size:40px;fill:var(--ink);}
  .banner-text{font-size:32px;fill:var(--paper);}
  .back{font-family:"Rubik",sans-serif;fill:var(--ink);}
  .back-brand{font-size:18px;}
  .back-body{font-size:14.5px;}
  .back-body .strong{font-weight:600;}
  .back-address{font-size:14.5px;}
  .back-web{font-size:14.5px;font-weight:600;}
  .arc-text{font-size:15.5px;}
  .arc-text .strong{font-weight:600;}
</style>
</head>
<body>
<div class="canvas">
<svg class="labels" width="1200" height="727" viewBox="0 0 1200 727" xmlns="http://www.w3.org/2000/svg">

  <!-- Deckeloberseite -->
  <g class="label-front">
    <circle cx="352" cy="345" r="201" fill="var(--orange)" stroke="var(--rim)" stroke-width="0.8"/>
    <text class="brand-top" x="350" y="255" text-anchor="middle">KELMAR.HOF</text>

    <rect class="branch-area" role="img" aria-label="Illustration eines Olivenzweigs mit zwei Blättern" x="164" y="268" width="132" height="70" rx="10" fill="var(--branch-area)"/>

    <circle class="badge" cx="464" cy="295" r="54" fill="var(--ink)"/>
    <text class="hand badge-text" x="466" y="291" text-anchor="middle" textLength="64" lengthAdjust="spacingAndGlyphs">NATUR-</text>
    <text class="hand badge-text" x="466" y="322" text-anchor="middle" textLength="80" lengthAdjust="spacingAndGlyphs">KOSMETIK</text>

    <text class="product-name" x="372" y="386" text-anchor="middle" textLength="290" lengthAdjust="spacingAndGlyphs">Velamira</text>
    <text class="hand subtitle" x="352" y="432" text-anchor="middle" textLength="320" lengthAdjust="spacingAndGlyphs">OLIVENÖL-INTENSIVCREME</text>

    <g transform="rotate(-5 360 480)">
      <rect x="250" y="437" width="205" height="38" fill="var(--ink)"/>
      <rect x="230" y="475" width="266" height="38" fill="var(--ink)"/>
      <text class="hand banner-text" x="354" y="467" text-anchor="middle" textLength="166" lengthAdjust="spacingAndGlyphs">BIO-OLIVE + VEGAN</text>
      <text class="hand banner-text" x="362" y="505" text-anchor="middle" textLength="218" lengthAdjust="spacingAndGlyphs">PFLEGE- UND SCHUTZCREME</text>
    </g>
  </g>

  <!-- Dosenboden -->
  <g class="label-back back">
    <circle cx="837" cy="337" r="201" fill="var(--paper)" stroke="var(--rim)" stroke-width="0.8"/>
    <text class="back-brand" x="837" y="222" text-anchor="middle">KELMAR.HOF</text>
    <g class="back-body" text-anchor="middle">
      <text x="837" y="246">wasserfreie Creme, unparfümiert</text>
      <text x="837" y="269"><tspan class="strong">Ingredients:</tspan> Olea Europaea Fruit Oil,</text>
      <text x="837" y="288">Hydrogenated Rapeseed Oil, Tocopherol</text>
      <text x="837" y="306"><tspan class="strong">Anwendung:</tspan> Sparsam auf die trockene Haut</text>
      <text x="837" y="325">auftragen (ergiebig!). Die Einwirkzeit kann einige</text>
      <text x="837" y="343">Minuten dauern, vorher kann es beim Berühren</text>
      <text x="837" y="362">von Gegenständen mit den gecremten Körper-</text>
      <text x="837" y="380">partien zur Fettübertragung kommen.</text>
    </g>
    <g class="back-address" text-anchor="middle">
      <text x="819" y="406">KELMAR.HOF</text>
      <text x="819" y="424">Dr. med. Marlene Holmer</text>
      <text x="819" y="443">Hafenweg 17 . D-24103 Kiel</text>
      <text class="back-web" x="819" y="463">www.KELMAR.HOF</text>
    </g>
    <rect role="img" aria-label="Recycling-Symbol" x="931" y="390" width="40" height="40" rx="6" fill="var(--ink)"/>

    <path id="back-arc" d="M661 394 A185 185 0 0 0 1010 403" fill="none"/>
    <text class="arc-text">
      <textPath href="#back-arc" startOffset="50%" text-anchor="middle">Made in Germany | Mind. haltbar: Januar 2021 | <tspan class="strong">150 ml</tspan></textPath>
    </text>
  </g>
</svg>
</div>
</body>
</html>
```